Clear Plastic Card Design

I am looking to have a business card designed from my logo icon. I am looking to match the style of a different business card I have attached in the files.
Looking for a card that is plastic, with layers of transparency in the shape of my logo icon (also attached in the files) - not a circle like the other card. The winning design will incorporate the red icon logo on the front and back and include the charity's name, "Light for the Weary Souls" in the same or similar font, as well as an email and phone number. For now, use the email: email@lightfortheweary-mail.org and the phone number 555-382-7194.
We like how the sample business card has transparency, partial and full opacity layers and a matching color scheme. Files will need to be in vector so that our business card printing company can work with it.
UPDATE:
We've some excellent designs in, thank you everyone! I got an early review from the owner, and he requested a minor redirect to find his perfect design. He wants the design to stand out by NOT being a rectangle. Try instead a circle, square, or best yet - something that falls in the outline of the logo icon, either fully or partially. Thank you, everyone!
Light for the Weary Souls text should be incorporated as well as a phone and email.

```html
<!DOCTYPE html>
<html lang="en">
<head>
<meta charset="utf-8">
<title>Light for the Weary Souls – Business Card</title>
<link href="https://fonts.googleapis.com/css2?family=Poppins:wght@400&family=Roboto:wght@300&display=swap" rel="stylesheet">
<style>
  :root {
    --page-bg: #e9e4de;
    --card-frost: #d9c7b6;
    --card-frost-light: #ebe1d7;
    --card-glow: rgba(222, 236, 244, 0.55);
    --card-edge: #c9b8a7;
    --decor-blush: rgba(205, 120, 100, 0.30);
    --brand-red: #d4262a;
    --brand-orange: #e8562b;
    --ink: #1b1b1b;
    --band: #1a1a1a;
    --band-grey: #a59a92;
    --band-red: #b8474a;
    --band-sand: #c7b6a4;
  }
  * { box-sizing: border-box; margin: 0; padding: 0; }
  html, body {
    width: 1200px;
    height: 969px;
    overflow: hidden;
    background: var(--page-bg);
  }
  .business-card {
    position: absolute;
    left: 60px;
    top: 177px;
    width: 1080px;
    height: 615px;
    background:
      radial-gradient(ellipse 140px 260px at 340px 250px, var(--card-glow), transparent 70%),
      radial-gradient(ellipse 120px 240px at 880px 300px, var(--card-glow), transparent 70%),
      radial-gradient(ellipse 260px 80px at 400px 470px, rgba(214, 120, 130, 0.25), transparent 70%),
      linear-gradient(160deg, var(--card-frost-light) 0%, var(--card-frost) 100%);
    border: 1px solid var(--card-edge);
    box-shadow: 0 6px 18px rgba(0, 0, 0, 0.18);
    overflow: hidden;
  }
  .watermark-name {
    position: absolute;
    left: 6px;
    top: 70px;
    font-family: "Poppins", sans-serif;
    font-weight: 400;
    font-size: 104px;
    line-height: 1.22;
    letter-spacing: -2px;
    color: var(--decor-blush);
    white-space: nowrap;
  }
  .brand-lockup {
    position: absolute;
    right: 60px;
    top: 80px;
    display: flex;
    align-items: flex-end;
    gap: 26px;
  }
  .brand-name {
    font-family: "Poppins", sans-serif;
    font-weight: 400;
    font-size: 31px;
    line-height: 1.2;
    color: var(--ink);
    text-align: left;
    white-space: nowrap;
    margin-bottom: 10px;
  }
  .brand-square {
    width: 190px;
    height: 190px;
    background: linear-gradient(135deg, var(--brand-red), var(--brand-orange));
  }
  .contact-band {
    position: absolute;
    left: 0;
    top: 496px;
    width: 100%;
    height: 60px;
    background: var(--band);
    display: flex;
    align-items: center;
    justify-content: center;
    gap: 14px;
    font-family: "Roboto", sans-serif;
    font-weight: 300;
    font-size: 24px;
  }
  .contact-phone { color: var(--band-grey); }
  .contact-email { color: var(--band-red); }
  .contact-web { color: var(--band-sand); }
  .contact-divider { color: var(--band-grey); }
</style>
</head>
<body>
  <div class="business-card">
    <p class="watermark-name" aria-hidden="true">Light for the<br>Weary Souls</p>

    <div class="brand-lockup">
      <p class="brand-name">Light for the<br>Weary Souls</p>
      <div class="brand-square" aria-hidden="true"></div>
    </div>

    <div class="contact-band">
      <span class="contact-phone">555-382-7194</span>
      <span class="contact-divider">|</span>
      <span class="contact-email">email@lightfortheweary-mail.org</span>
      <span class="contact-divider">|</span>
      <span class="contact-web">lightforthewearysouls-web.org</span>
    </div>
  </div>
</body>
</html>
```